Car transport business

We need a new business card design. Attached is our old card sample. I would just like to adjust the logo colors (blue and red) to be brighter. I changed my name to the brighter red and the word dispatcher to a brighter blue as an example. But you can adjust those colors further. And then perhaps you can use the same colors for the card design but use your imagination.

As a suggestion so the card stands out I would like to add a clip art of car carrier truck. Attached are examples of that as well

```html
<!DOCTYPE html>
<html lang="en">
<head>
<meta charset="utf-8">
<title>Vantage Haul — Business Card</title>
<link rel="stylesheet" href="https://fonts.googleapis.com/css2?family=Arimo:wght@400;700&display=swap">
<style>
  :root {
    --stage: #3a3a3c;
    --brand-blue: #1f78c8;
    --brand-blue-deep: #1a66ad;
    --brand-red: #e8202a;
    --paper: #ffffff;
    --ink: #111111;
  }
  * { margin: 0; padding: 0; box-sizing: border-box; }
  html, body {
    width: 1200px; height: 1015px; overflow: hidden;
    background: var(--stage);
    font-family: "Arimo", Arial, sans-serif;
  }
  .canvas { position: relative; width: 1200px; height: 1015px; }

  .card {
    position: absolute; width: 700px; height: 400px; overflow: hidden;
    box-shadow: 0 14px 30px rgba(0,0,0,.45);
  }

  /* Back side */
  .card-back { left: 110px; top: 110px; background: var(--brand-blue); }
  .back-pattern {
    position: absolute; inset: 0;
    background: linear-gradient(135deg, #2384d6 0%, #1c70bd 100%);
  }
  .back-wordmark {
    position: absolute; left: 50%; top: 50%; transform: translate(-50%, -50%);
    display: flex; align-items: center; gap: 14px;
  }
  .back-wordmark .mark-dot { width: 30px; height: 30px; border-radius: 50%; background: var(--paper); }
  .back-wordmark .wordmark-name {
    font-weight: 700; font-size: 46px; letter-spacing: 3px; color: var(--paper); text-transform: uppercase;
  }

  /* Front side */
  .card-front { left: 390px; top: 505px; background: var(--paper); }
  .front-logo {
    position: absolute; left: 190px; top: 46px;
    display: flex; align-items: center; gap: 14px;
  }
  .front-logo .mark-dot { width: 34px; height: 34px; border-radius: 50%; background: var(--brand-red); }
  .front-logo .wordmark-name {
    font-weight: 700; font-size: 44px; letter-spacing: 3px; color: var(--brand-blue); text-transform: uppercase; line-height: 1;
  }
  .tagline {
    position: absolute; left: 238px; top: 100px;
    font-size: 12px; letter-spacing: 3.2px; color: var(--brand-blue); text-transform: uppercase;
  }
  .carrier-art {
    position: absolute; right: 0; top: 140px; width: 330px; height: 210px;
    background: linear-gradient(180deg, #2a2a2a 0%, #0e0e0e 100%);
    border-top-left-radius: 30px;
  }
  .contact {
    position: absolute; left: 44px; top: 226px; color: var(--brand-blue);
  }
  .person-name { font-size: 36px; font-weight: 400; letter-spacing: 1px; line-height: 1; text-transform: uppercase; }
  .person-name .surname { color: var(--brand-red); }
  .person-role { font-size: 15px; letter-spacing: 1px; margin-top: 4px; text-transform: uppercase; }
  .contact-list { list-style: none; margin-top: 18px; }
  .contact-list li {
    display: flex; align-items: center; gap: 10px;
    font-size: 17px; color: var(--brand-red); line-height: 24px;
  }
  .contact-list svg { width: 16px; height: 16px; fill: var(--brand-blue); flex: none; }
  .base-band { position: absolute; left: 0; right: 0; bottom: 0; height: 12px; background: var(--brand-blue); }
</style>
</head>
<body>
<main class="canvas">

  <section class="card card-back" aria-label="Business card, back side">
    <div class="back-pattern" role="img" aria-label="Repeating embossed brand pattern on blue"></div>
    <div class="back-wordmark">
      <span class="mark-dot"></span>
      <span class="wordmark-name">Vantage Haul</span>
    </div>
  </section>

  <section class="card card-front" aria-label="Business card, front side">
    <div class="front-logo">
      <span class="mark-dot"></span>
      <span class="wordmark-name">Vantage Haul</span>
    </div>
    <p class="tagline">The auto transport professionals</p>

    <div class="carrier-art" role="img" aria-label="Silhouette illustration of a car carrier truck loaded with cars"></div>

    <div class="contact">
      <h1 class="person-name">Omar <span class="surname">Reddick</span></h1>
      <p class="person-role">Diapatcher</p>
      <ul class="contact-list">
        <li>
          <svg viewBox="0 0 24 24" aria-hidden="true"><path d="M6.6 10.8a15 15 0 0 0 6.6 6.6l2.2-2.2c.3-.3.7-.4 1-.2 1.1.4 2.3.6 3.6.6.6 0 1 .4 1 1V20c0 .6-.4 1-1 1A17 17 0 0 1 3 4c0-.6.4-1 1-1h3.5c.6 0 1 .4 1 1 0 1.3.2 2.5.6 3.6.1.3 0 .7-.2 1z"/></svg>
          555-201-4830
        </li>
        <li>
          <svg viewBox="0 0 24 24" aria-hidden="true"><path d="M7 3h8v5H7zM4 9h16a2 2 0 0 1 2 2v6h-4v4H6v-4H2v-6a2 2 0 0 1 2-2zm4 7v3h8v-3z"/></svg>
          555-201-4871
        </li>
        <li>
          <svg viewBox="0 0 24 24" aria-hidden="true"><path d="M2 5h20v14H2zm2 2v.5l8 5 8-5V7l-8 5z"/></svg>
          vantagehaulco@mail.com
        </li>
      </ul>
    </div>

    <div class="base-band"></div>
  </section>

</main>
</body>
</html>
```